Business card design and logo for hot water plumbing business

I need a logo and business card for my business which installs hot water heaters
Must have on front:
Bramblefield Hot Water Solutions
Gareth Pennick
0417382946

Either front or back:
gareth@bramblefieldhotwatersolutions.com.au
ABN 48276153094
Licence No 583214K

On the back in point form:
Supply and installation of
• electric storage
• gas storage/instantaneous
• heat pumps
• solar heaters

Iv provided 3 examples of cards I like but open to different ideas.

```html
<!DOCTYPE html>
<html lang="en">
<head>
<meta charset="utf-8">
<title>Bramblefield Hot Water Solutions – Business Cards</title>
<link rel="stylesheet" href="https://fonts.googleapis.com/css2?family=Exo+2:wght@400;600;800&display=swap">
<style>
  :root {
    --bg: #5a5d61;
    --card: #ffffff;
    --ink: #2b2b2b;
    --brand: #1f8cc4;
    --navy: #24384a;
    --band-dark: #3a3b3d;
    --band-light: #d6d7d8;
    --muted: #eeeeee;
  }
  * { box-sizing: border-box; margin: 0; padding: 0; }
  html, body { width: 1200px; height: 974px; overflow: hidden; }
  body {
    background: var(--bg);
    font-family: "Exo 2", sans-serif;
    color: var(--ink);
    position: relative;
  }
  .card {
    position: absolute;
    top: 137px;
    width: 400px;
    height: 700px;
    background: var(--card);
    overflow: hidden;
    box-shadow: 0 14px 30px rgba(0,0,0,.35);
  }
  .card--back { left: 160px; }
  .card--front { left: 640px; }

  .logo {
    position: absolute;
    left: 0; right: 0;
    display: flex;
    flex-direction: column;
    align-items: center;
    gap: 8px;
  }
  .card--back .logo { top: 90px; }
  .card--front .logo { top: 52px; }
  .logo__mark {
    width: 58px; height: 58px;
    border-radius: 50%;
    background: var(--brand);
  }
  .logo__name {
    font-weight: 800;
    font-size: 17px;
    color: var(--brand);
    text-transform: uppercase;
    text-align: center;
    line-height: 1.15;
    letter-spacing: .5px;
  }
  .logo__tagline {
    font-size: 9px;
    color: var(--ink);
  }

  .services {
    position: absolute;
    top: 300px;
    left: 60px; right: 60px;
    font-size: 15px;
    line-height: 1.6;
  }
  .services__heading {
    font-weight: 600;
    font-size: 15px;
    color: var(--navy);
    margin-bottom: 6px;
  }
  .services__list { list-style: none; }
  .services__list li { display: flex; align-items: center; gap: 10px; }
  .services__list li::before {
    content: "";
    width: 7px; height: 7px;
    border-radius: 50%;
    background: var(--brand);
    flex: none;
  }
  .credentials {
    position: absolute;
    top: 500px;
    left: 60px; right: 60px;
    padding-top: 14px;
    border-top: 1px solid var(--band-light);
    font-size: 13px;
    line-height: 1.7;
    color: var(--ink);
  }

  .web-band {
    position: absolute;
    left: 0; right: 0; bottom: 0;
    height: 96px;
    background: var(--navy);
    border-radius: 28px 28px 0 0;
    display: flex;
    align-items: center;
    justify-content: center;
    color: #fff;
    font-size: 16px;
    letter-spacing: .5px;
  }

  .name-band {
    position: absolute;
    top: 200px; left: 0; right: 0;
    height: 92px;
    background: linear-gradient(180deg, #4a4b4d, var(--band-dark));
    color: #fff;
    text-align: right;
    padding: 20px 34px 0 0;
  }
  .name-band__name { font-size: 26px; font-weight: 600; letter-spacing: 1px; text-transform: uppercase; }
  .name-band__role { font-size: 16px; letter-spacing: 1.5px; text-transform: uppercase; margin-top: 2px; }

  .contact-row {
    position: absolute;
    left: 0; right: 0;
    display: flex;
    align-items: center;
    padding-left: 34px;
    gap: 22px;
    font-size: 15px;
  }
  .contact-row svg { flex: none; }
  .contact-row--phone { top: 292px; height: 96px; background: var(--card); }
  .contact-row--email { top: 388px; height: 84px; background: var(--band-light); font-size: 12.5px; }
  .contact-row--address { top: 472px; height: 110px; background: var(--muted); }
  .contact-row__lines { line-height: 1.45; }
</style>
</head>
<body>

  <section class="card card--back" aria-label="Card back">
    <div class="logo">
      <div class="logo__mark"></div>
      <div class="logo__name">Bramblefield<br>Hot Water Solutions</div>
      <div class="logo__tagline">Your Trusted Local Hot Water Team</div>
    </div>

    <div class="services">
      <div class="services__heading">Supply and installation of</div>
      <ul class="services__list">
        <li>Electric storage</li>
        <li>Gas storage / instantaneous</li>
        <li>Heat pumps</li>
        <li>Solar heaters</li>
      </ul>
    </div>

    <div class="credentials">
      <div>ABN 48276153094</div>
      <div>Licence No 583214K</div>
    </div>

    <div class="web-band">www.bramblefieldhotwater.com.au</div>
  </section>

  <section class="card card--front" aria-label="Card front">
    <div class="logo">
      <div class="logo__mark"></div>
      <div class="logo__name">Bramblefield<br>Hot Water Solutions</div>
      <div class="logo__tagline">Your Trusted Local Hot Water Team</div>
    </div>

    <div class="name-band">
      <div class="name-band__name">Gareth Pennick</div>
      <div class="name-band__role">General Manager</div>
    </div>

    <div class="contact-row contact-row--phone">
      <svg width="32" height="26" viewBox="0 0 32 26" aria-hidden="true">
        <path d="M2 8 Q16 0 30 8 L27 12 L22 10 L22 7 Q16 5 10 7 L10 10 L5 12 Z" fill="#222"/>
        <path d="M8 13 L24 13 L29 25 L3 25 Z" fill="#222"/>
        <circle cx="16" cy="19" r="3.5" fill="#fff"/>
      </svg>
      <div class="contact-row__lines">0417 382 946<br>02 6184 3927</div>
    </div>

    <div class="contact-row contact-row--email">
      <svg width="30" height="22" viewBox="0 0 30 22" aria-hidden="true">
        <rect x="1" y="1" width="28" height="20" fill="#222"/>
        <path d="M2 2 L15 12 L28 2" fill="none" stroke="#d6d7d8" stroke-width="1.6"/>
      </svg>
      <div>gareth@bramblefieldhotwatersolutions.com.au</div>
    </div>

    <div class="contact-row contact-row--address">
      <svg width="30" height="34" viewBox="0 0 24 34" aria-hidden="true">
        <path d="M12 1 C5 1 1 6 1 12 C1 20 12 33 12 33 C12 33 23 20 23 12 C23 6 19 1 12 1 Z" fill="#222"/>
        <circle cx="12" cy="12" r="4.5" fill="#eee"/>
      </svg>
      <div class="contact-row__lines">14 Kestrel Lane,<br>Unit 3 Harwood Street</div>
    </div>

    <div class="web-band">www.bramblefieldhotwater.com.au</div>
  </section>

</body>
</html>
```